Create modern and sleek business card for luxury real estate company

We're a "boutique" real estate office looking for a design that gets across a highly modern luxury brand. Blacks and whites are probably the best colors unless we try a silver foil for the logo. I've attached a version of our current logo here. I'd like to swap out the current font on there with Gotham Light Regular.

I'm looking to have one side of the card have the logo with the space for our agents info on the other side.

Target Market(s)

Young professionals in a "luxury" headspace

Industry/Entity Type

Real estate

Contact Information for Business Card

A place for agent name, cell number, website. The slogan "Quietly Redefining Fine Homes".

Font styles to use
Other font styles liked:
• Gotham Regular

Colors

Designer to choose only greyscale colors for use in the design.

Requirements
Must have
• Matte black as the background color. Clean lines and use of contrast. A specific design aspect that will use silver foil.
Nice to have
• Up in the air on integrating a QR code
Should not have
• Any houses or other real estate related design (ex: a clip art house)

```html
<!DOCTYPE html>
<html lang="en">
<head>
<meta charset="UTF-8">
<title>Lumen Estates – Business Card</title>
<link href="https://fonts.googleapis.com/css2?family=Open+Sans:wght@400;700&display=swap" rel="stylesheet">
<style>
  :root {
    --backdrop: #3b3b3b;
    --matte-black: #111111;
    --card-edge: #1c1c1c;
    --ink-white: #f2f2f2;
    --ink-grey: #8a8a8a;
    --foil-silver: #b9b9b9;
    --foil-dark: #4a4a4a;
    --rule: #6a6a6a;
  }
  * { margin: 0; padding: 0; box-sizing: border-box; }
  html, body { width: 1200px; height: 801px; overflow: hidden; }
  body {
    background: var(--backdrop);
    font-family: "Open Sans", Arial, sans-serif;
    position: relative;
  }
  .card {
    position: absolute;
    top: 263px;
    width: 480px;
    height: 274px;
    background: var(--matte-black);
    border: 1px solid var(--card-edge);
    box-shadow: 0 14px 30px rgba(0,0,0,0.45);
  }
  .card--front { left: 90px; }
  .card--back  { left: 630px; }

  /* Agent side */
  .brand {
    position: absolute;
    left: 34px;
    top: 102px;
    display: flex;
    align-items: center;
    gap: 12px;
  }
  .brand__circle {
    width: 52px; height: 52px;
    border: 2px solid var(--ink-white);
    border-radius: 50%;
  }
  .brand__name {
    color: var(--ink-white);
    font-weight: 400;
    font-size: 19px;
    letter-spacing: 1px;
    line-height: 1.15;
    text-transform: uppercase;
  }
  .divider {
    position: absolute;
    left: 228px;
    top: 78px;
    width: 1px;
    height: 104px;
    background: var(--rule);
  }
  .agent {
    position: absolute;
    left: 246px;
    top: 74px;
  }
  .agent__name {
    color: var(--ink-white);
    font-weight: 700;
    font-size: 15px;
    letter-spacing: 0.5px;
    text-transform: uppercase;
  }
  .agent__title {
    color: var(--ink-grey);
    font-size: 11px;
    margin-bottom: 8px;
  }
  .contact { list-style: none; }
  .contact__item {
    display: flex;
    align-items: center;
    gap: 7px;
    color: var(--ink-white);
    font-size: 11px;
    line-height: 19px;
  }
  .contact__icon { width: 10px; height: 10px; }
  .slogan {
    position: absolute;
    left: 246px;
    bottom: 40px;
    color: var(--ink-white);
    font-size: 11px;
  }

  /* Brand side */
  .foil-ring {
    position: absolute;
    left: 18px;
    top: 22px;
    width: 230px;
    height: 230px;
  }
  .back-name {
    position: absolute;
    left: 282px;
    top: 106px;
    color: var(--foil-silver);
    font-weight: 400;
    font-size: 26px;
    letter-spacing: 1px;
    line-height: 1.2;
    text-transform: uppercase;
  }
</style>
</head>
<body>
  <section class="card card--front" aria-label="Business card, agent side">
    <div class="brand">
      <span class="brand__circle"></span>
      <span class="brand__name">Lumen<br>Estates</span>
    </div>
    <div class="divider"></div>
    <div class="agent">
      <p class="agent__name">Daniel Averly</p>
      <p class="agent__title">President</p>
      <ul class="contact">
        <li class="contact__item">
          <svg class="contact__icon" viewBox="0 0 10 10"><path fill="#f2f2f2" d="M2 0.5 L3.6 0.5 L4.2 2.8 L3 3.6 Q4 5.8 6.4 7 L7.2 5.8 L9.5 6.4 L9.5 8 Q9.5 9.5 8 9.5 Q0.5 9 0.5 2 Q0.5 0.5 2 0.5Z"/></svg>
          555-013-2468
        </li>
        <li class="contact__item">
          <svg class="contact__icon" viewBox="0 0 10 10"><path d="M0.5 2 H9.5 V8.5 H0.5Z M0.5 2 L5 5.5 L9.5 2" fill="none" stroke="#f2f2f2" stroke-width="1"/></svg>
          daverly@lumenestates.com
        </li>
        <li class="contact__item">
          <svg class="contact__icon" viewBox="0 0 10 10"><circle cx="5" cy="5" r="4.5" fill="none" stroke="#f2f2f2" stroke-width="1"/><path d="M0.5 5 H9.5 M5 0.5 Q2.5 5 5 9.5 M5 0.5 Q7.5 5 5 9.5" fill="none" stroke="#f2f2f2" stroke-width="0.8"/></svg>
          www.lumenestates.com
        </li>
      </ul>
    </div>
    <p class="slogan">Quietly Redefining Fine Homes</p>
  </section>

  <section class="card card--back" aria-label="Business card, brand side">
    <svg class="foil-ring" viewBox="0 0 230 230" aria-hidden="true">
      <defs>
        <linearGradient id="foil" x1="0" y1="0" x2="1" y2="1">
          <stop offset="0" stop-color="#4a4a4a"/>
          <stop offset="0.55" stop-color="#2a2a2a"/>
          <stop offset="1" stop-color="#b9b9b9"/>
        </linearGradient>
      </defs>
      <circle cx="115" cy="115" r="108" fill="none" stroke="url(#foil)" stroke-width="6"/>
    </svg>
    <p class="back-name">Lumen<br>Estates</p>
  </section>
</body>
</html>
```